I am looking to create a newly designed website for our national leadership conference which is entitled, "The Harbor of Momentum Leadership Summit". The Harbor of Momentum Leadership Summit is a national conference for student leaders that prepares them for career leadership success. The current website can be seen at www.harborofmomentumleadershipsummit.com.

My goal for the new site is to create a more updated, fresh, hip, and exciting look that appeals to the younger generation while also maintaining are professional appeal. The color should be black, white, and gold. We want there to be live videos played and places to insert pictures for the panels as well.

I look forward to seeing you the new creations.

Requirements
Must have
• Ability to play videos on the home page and throughout the website. Also, make sure that the website shows up clearly on an zTablet.
Nice to have
• Nice look

```html
<!DOCTYPE html>
<html lang="en">
<head>
<meta charset="utf-8">
<title>Harbor of Momentum Leadership Summit</title>
<link rel="stylesheet" href="https://fonts.googleapis.com/css2?family=Raleway:wght@400;500;600;700&family=Arimo:wght@400;700&display=swap">
<style>
  :root {
    --gold: #c99a3e;
    --gold-light: #d6a84c;
    --black: #000000;
    --ink: #1b1b1b;
    --white: #ffffff;
    --paper: #f4f4f4;
    --line: #dcdcdc;
    --footer: #161616;
    --footer-bar: #0e0e0e;
    --muted: #6c6c6c;
    --hero-dark: #2a2e38;
  }
  * { margin: 0; padding: 0; box-sizing: border-box; }
  html, body { width: 1200px; height: 2439px; overflow: hidden; }
  body { position: relative; background: var(--white); font-family: "Arimo", Arial, sans-serif; color: var(--ink); }
  section, header, footer { position: absolute; left: 0; width: 1200px; }
  .heading { font-family: "Raleway", sans-serif; font-weight: 400; color: var(--gold); text-align: center; text-transform: uppercase; letter-spacing: 0.5px; }

  /* header */
  .site-header { top: 0; height: 125px; background: var(--white); }
  .brand { position: absolute; left: 112px; top: 28px; display: flex; align-items: center; gap: 10px; }
  .brand-mark { width: 20px; height: 20px; border-radius: 50%; background: var(--gold); }
  .brand-name { font-family: "Raleway", sans-serif; font-weight: 700; font-size: 17px; letter-spacing: 1px; color: var(--ink); }
  .main-nav { position: absolute; left: 351px; top: 47px; display: flex; gap: 0; }
  .main-nav a { display: block; height: 38px; line-height: 38px; padding: 0 15px; font-size: 13.5px; color: var(--ink); text-decoration: none; text-transform: uppercase; margin-right: 8px; }
  .main-nav a.active { background: var(--gold); color: var(--white); font-weight: 700; border-radius: 3px; }

  /* hero */
  .hero { top: 125px; height: 475px; }
  .hero-photo { position: absolute; inset: 0; background: linear-gradient(180deg, #3b3f4a 0%, #2b2e37 55%, #1e2028 100%); }
  .hero-title { position: absolute; top: 174px; width: 100%; text-align: center; font-family: "Raleway", sans-serif; font-weight: 600; font-size: 25px; color: var(--white); }
  .play { position: absolute; left: 571px; top: 241px; }
  .dots { position: absolute; width: 100%; display: flex; justify-content: center; gap: 11px; }
  .dots span { width: 8px; height: 8px; border-radius: 50%; background: var(--white); }
  .dots span.on { background: var(--gold); }
  .dots.grey span { background: #8a8a8a; }
  .dots.grey span.on { background: var(--gold); }
  .hero .dots { top: 445px; }

  /* register */
  .register { top: 600px; height: 257px; background: var(--paper); }
  .register h2 { position: absolute; top: 28px; width: 100%; font-size: 32px; }
  .register h2 strong { font-weight: 700; }
  .register p { position: absolute; left: 225px; top: 78px; width: 750px; font-family: "Raleway", sans-serif; font-size: 12.5px; line-height: 21px; text-align: center; color: #222; }
  .countdown-title { position: absolute; top: 142px; width: 100%; font-size: 17px; }
  .countdown { position: absolute; left: 530px; top: 179px; display: flex; gap: 3px; }
  .unit { width: 50px; height: 52px; border-radius: 3px; overflow: hidden; }
  .unit b { display: block; height: 31px; line-height: 31px; background: linear-gradient(#3a3a3a, #151515); color: var(--white); font-size: 16px; text-align: center; }
  .unit small { display: block; height: 21px; line-height: 21px; background: var(--gold); color: var(--white); font-size: 7px; font-weight: 700; text-align: center; text-transform: uppercase; }

  /* award */
  .award { top: 857px; height: 184px; background: var(--white); }
  .award h2 { position: absolute; top: 30px; width: 100%; font-size: 24px; line-height: 31px; }
  .award-badge { position: absolute; left: 525px; top: 118px; width: 150px; height: 24px; background: #e6e6e6; border-radius: 2px; }

  /* logo rows */
  .partners { top: 1041px; height: 278px; background: var(--black); }
  .schools { top: 1319px; height: 312px; background: var(--paper); }
  .partners h2 { position: absolute; top: 28px; width: 100%; font-size: 24px; }
  .schools h2 { position: absolute; top: 39px; width: 100%; font-size: 24px; }
  .logo-row { position: absolute; left: 99px; width: 1002px; height: 98px; display: flex; background: var(--white); border: 1px solid var(--line); }
  .logo-row li { list-style: none; flex: 1; display: flex; align-items: center; justify-content: center; border-right: 1px solid var(--line); font-family: "Raleway", sans-serif; font-weight: 600; font-size: 14px; color: #333; text-align: center; padding: 0 8px; }
  .logo-row li:last-child { border-right: 0; }
  .partners .logo-row { top: 97px; }
  .partners .dots { top: 222px; }
  .schools .logo-row { top: 120px; }
  .schools .dots { top: 254px; }

  /* video */
  .moments { top: 1631px; height: 512px; background: var(--black); }
  .moments h2 { position: absolute; top: 39px; width: 100%; font-size: 24px; line-height: 31px; }
  .video { position: absolute; left: 299px; top: 133px; width: 600px; height: 334px; background: linear-gradient(160deg, #6e6c66 0%, #4c4a45 50%, #2f2d2a 100%); }
  .video .play { left: 271px; top: 138px; }

  /* footer */
  .site-footer { top: 2143px; height: 247px; background: var(--footer); color: #ddd; }
  .col { position: absolute; top: 30px; }
  .col h3 { font-family: "Raleway", sans-serif; font-weight: 700; font-size: 14px; color: var(--white); margin-bottom: 14px; }
  .col-about { left: 137px; width: 240px; }
  .col-about p { font-size: 10.5px; line-height: 20px; color: #5e5e5e; }
  .subscribe { margin-top: 12px; width: 240px; height: 32px; background: #262626; border-radius: 4px; display: flex; align-items: center; justify-content: space-between; padding: 0 6px 0 12px; font-size: 10.5px; font-style: italic; color: #777; }
  .subscribe span.go { width: 22px; height: 22px; background: var(--gold); border-radius: 3px; display: flex; align-items: center; justify-content: center; }
  .col-nav { left: 446px; }
  .col-nav ul { list-style: none; }
  .col-nav li { font-size: 10.5px; line-height: 20.7px; color: #888; text-transform: uppercase; display: flex; align-items: center; gap: 12px; }
  .col-nav li::before { content: "»"; color: var(--gold); font-size: 12px; }
  .col-news { left: 600px; width: 205px; }
  .news-item { display: flex; gap: 12px; padding-bottom: 10px; margin-bottom: 10px; border-bottom: 1px solid #2a2a2a; }
  .news-item:last-child { border-bottom: 0; }
  .news-thumb { width: 50px; height: 44px; background: linear-gradient(135deg, #8a7a68, #4c4540); border-radius: 2px; flex: none; }
  .news-item h4 { font-family: "Raleway", sans-serif; font-weight: 600; font-size: 13.5px; line-height: 19px; color: #e8e8e8; }
  .news-item time { display: block; font-size: 9px; color: #999; margin-top: 4px; }
  .col-tweets { left: 841px; width: 240px; }
  .tweet { font-size: 10.5px; line-height: 19px; color: #666; margin-bottom: 12px; }
  .tweet .handle { color: var(--gold); font-weight: 700; }
  .tweet .handle::before { content: ""; display: inline-block; width: 8px; height: 8px; border-radius: 50%; background: var(--gold); margin-right: 5px; }
  .tweet time { display: block; font-size: 9px; color: #999; margin-top: 2px; }

  .footer-bar { top: 2390px; height: 49px; background: var(--footer-bar); }
  .footer-bar small { position: absolute; left: 133px; top: 18px; font-size: 9.5px; color: #888; }
  .social { position: absolute; left: 870px; top: 13px; display: flex; gap: 13px; list-style: none; }
  .social li { width: 22px; height: 22px; border: 1px solid #333; border-radius: 3px; background: #1c1c1c; }
</style>
</head>
<body>

<header class="site-header">
  <div class="brand"><span class="brand-mark"></span><span class="brand-name">HARBOR OF MOMENTUM</span></div>
  <nav class="main-nav">
    <a class="active" href="#">Home</a><a href="#">About</a><a href="#">Conference</a><a href="#">Register</a><a href="#">Testimonials</a><a href="#">Y Factor</a><a href="#">Videos</a><a href="#">Contact</a>
  </nav>
</header>

<section class="hero">
  <div class="hero-photo" role="img" aria-label="Photo of student leaders mingling at a conference reception"></div>
  <h1 class="hero-title">HARBOR OF MOMENTUM</h1>
  <svg class="play" width="58" height="58" viewBox="0 0 58 58"><circle cx="29" cy="29" r="27" fill="none" stroke="rgba(255,255,255,0.55)" stroke-width="2.5"/><path d="M24 19 L38 29 L24 39 Z" fill="rgba(255,255,255,0.55)"/></svg>
  <div class="dots"><span></span><span class="on"></span><span></span></div>
</section>

<section class="register">
  <h2 class="heading">Register <strong>Now</strong></h2>
  <p>for a transformational leadership experience that will connect you with an incredible diverse leadership network of students and professionals that provide you with the inspiration and leadership/professional skills needed to take your life to the next level!</p>
  <h3 class="heading countdown-title">6th Annual Conference Countdown</h3>
  <div class="countdown">
    <div class="unit"><b>00</b><small>Hours</small></div>
    <div class="unit"><b>00</b><small>Minutes</small></div>
    <div class="unit"><b>00</b><small>Seconds</small></div>
  </div>
</section>

<section class="award">
  <h2 class="heading">Voted as top student leadership<br>program of the year in 2014</h2>
  <div class="award-badge" role="img" aria-label="Award badge"></div>
</section>

<section class="partners">
  <h2 class="heading">Network with executives</h2>
  <ul class="logo-row">
    <li>Velvet Rook</li><li>Korvan Group</li><li>Pelliton</li><li>Marisol Media</li><li>Brightwell</li><li>Tidewater Works</li>
  </ul>
  <div class="dots"><span></span><span class="on"></span><span></span></div>
</section>

<section class="schools">
  <h2 class="heading">Connect with other student leaders from</h2>
  <ul class="logo-row">
    <li>Ridgeline State</li><li>Elmwick University</li><li>Caldera College</li><li>Southmere University</li><li>Ashford Institute</li><li>Westhaven University</li>
  </ul>
  <div class="dots grey"><span></span><span class="on"></span><span></span></div>
</section>

<section class="moments">
  <h2 class="heading">Experience transformational moments<br>like these student leaders</h2>
  <div class="video">
    <div style="position:absolute;inset:0" role="img" aria-label="Video still of students in a group discussion around a table"></div>
    <svg class="play" width="58" height="58" viewBox="0 0 58 58"><circle cx="29" cy="29" r="27" fill="none" stroke="rgba(255,255,255,0.55)" stroke-width="2.5"/><path d="M24 19 L38 29 L24 39 Z" fill="rgba(255,255,255,0.55)"/></svg>
  </div>
</section>

<footer class="site-footer">
  <div class="col col-about">
    <h3>About Us</h3>
    <p>Our summit gathers student leaders from campuses nationwide to build skills, meet mentors and grow lasting networks. Join us each year for talks, panels and hands-on workshops that shape tomorrow's leaders.</p>
    <div class="subscribe"><span>Subscribe Our Newsletter</span><span class="go"><svg width="8" height="8" viewBox="0 0 8 8"><path d="M2 1 L6 4 L2 7 Z" fill="#fff"/></svg></span></div>
  </div>
  <div class="col col-nav">
    <h3>Navigation</h3>
    <ul><li>Home</li><li>About</li><li>Conference</li><li>Register</li><li>Testimonials</li><li>Y Factor</li><li>Videos</li><li>Contact</li></ul>
  </div>
  <div class="col col-news">
    <h3>Our News</h3>
    <div class="news-item"><div class="news-thumb" role="img" aria-label="News photo of a leadership session"></div><div><h4>Leadership Lorium ipsum deo</h4><time>On Feb 12-2015</time></div></div>
    <div class="news-item"><div class="news-thumb" role="img" aria-label="News photo of a leadership session"></div><div><h4>Leadership Lorium ipsum deo</h4><time>On Feb 12-2015</time></div></div>
  </div>
  <div class="col col-tweets">
    <h3>Latest Tweets</h3>
    <div class="tweet"><span class="handle">@ Lumra</span> Registration for this year's summit is open now, save your seat today.<time>2 hours ago</time></div>
    <div class="tweet"><span class="handle">@ Lumra</span> New speaker lineup announced, see who joins our panels this fall.<time>2 hours ago</time></div>
  </div>
</footer>

<footer class="footer-bar">
  <small>Copyright© 2015. All Rights Reserved.</small>
  <ul class="social"><li></li><li></li><li></li><li></li><li></li><li></li></ul>
</footer>

</body>
</html>
```